Wix Design for a Clothing Design Web Marketing Site

We need a Wix design and content (including any images and copy) for a clothing design web storefront, Sew To Suit (or sewtosuit). Rough ideas and content can be found at http://marenvoltis.wix.com/sewtosuit.

Sew To Suit is an innovative business concept that combines fashion and entertainment. The business model allows customers to actively participate in the creation of fashion designs/concepts , visualize the garment in the customer’s body in 3D, and buy the physical garment made specially to fit the customer.
The fashion consultant will be able to create the design based on client's desires and test various possibilities (size, fabric, cut, etc..) in front of the customer, using software Drapova (the software is a key component of this business model)
(when developing the website use images from Drapova)
After the design is created, the customer can choose to order the actual piece. The garment will be made according to the created design, the customer measurements.

Target Market(s)

Primarily women from 25 to 45, who are fashion enthusiasts and appreciate fit and exclusivity. They are hedonistic shoppers, who shop for entertainment.
Men (metrosexuals) who are fashion enthusiasts, also hedonistic shoppers.

Industry/Entity Type

Clothing

Font styles to use
Serif
Sans Serif

Requirements
Must have
• Must have a landing page (home) or section, that gives the consumer an idea of what Sew To Suit will do for them, an about page or section that tells about the company and product, a how it works page or section that describes how it works (http://marenvoltis.wix.com/sewtosuit#!services3/c192y), and page or section about pricing, and a page or section on how to contact us.
Nice to have
• Very modern and clean. The website must be based on the main picture of the studio in the example. If that studio is the store, what will the website look like?
• Colors yellow, grey and white. Use the zig zag in yellow and white. You can change the size of the lines. The zig zagi gives the modern and bold accent. Outfits in pictures must show nicely tailored garments.

```html
<!DOCTYPE html>
<html lang="en">
<head>
<meta charset="utf-8">
<title>Sew To Suit – How It Works?</title>
<link href="https://fonts.googleapis.com/css2?family=Federo&family=Roboto+Slab:wght@300;400&family=Roboto+Condensed:wght@400&family=Open+Sans:ital,wght@0,400;0,700;1,400&display=swap" rel="stylesheet">
<style>
  :root {
    --ink: #1c1c1c;
    --charcoal: #232323;
    --night: #141414;
    --slate: #55575b;
    --nav: #6b6f78;
    --nav-active: #262626;
    --yellow: #f2e12c;
    --yellow-soft: #f6d64a;
    --pale: #fbeef0;
    --white: #ffffff;
    --muted: #8d8d8d;
    --text: #3f3f3f;
    --serif: "Roboto Slab", Georgia, serif;
    --display: "Federo", Georgia, serif;
    --sans: "Open Sans", Arial, sans-serif;
    --cond: "Roboto Condensed", Arial, sans-serif;
  }
  * { box-sizing: border-box; margin: 0; padding: 0; }
  html, body { width: 791px; height: 1200px; overflow: hidden; background: var(--white); }
  body { position: relative; font-family: var(--sans); color: var(--text); }

  /* Header */
  .site-header { position: absolute; left: 0; top: 0; width: 791px; height: 125px; }
  .header-band { position: absolute; inset: 0; }
  .brand { position: absolute; left: 48px; top: 10px; width: 195px; text-align: center; }
  .brand-dot { display: block; width: 92px; height: 92px; margin: 0 auto -6px; border-radius: 50%; background: #b3b3b3; }
  .brand-name { display: inline-block; background: var(--white); padding: 0 6px; font-family: var(--serif); font-weight: 400; font-size: 21px; color: var(--ink); letter-spacing: 1px; }
  .tagline { position: absolute; left: 373px; top: 26px; width: 410px; font-family: var(--display); font-size: 33px; line-height: 35px; color: var(--white); }

  /* Navigation */
  .main-nav { position: absolute; left: 0; top: 125px; width: 791px; height: 29px; background: var(--nav); }
  .main-nav a { position: absolute; top: 0; height: 29px; line-height: 29px; font-family: var(--cond); font-size: 12.5px; color: var(--white); text-decoration: none; text-align: center; }
  .main-nav a.is-active { background: var(--nav-active); }

  /* Page title band */
  .page-hero { position: absolute; left: 0; top: 154px; width: 791px; height: 87px; background: linear-gradient(180deg, #1f1f1f, #161616); }
  .page-hero h1 { position: absolute; left: 0; right: 0; top: 33px; text-align: center; font-family: var(--serif); font-weight: 400; font-size: 22px; color: var(--yellow); }

  /* Side decoration */
  .side-zigzag { position: absolute; top: 241px; width: 60px; height: 777px; background: linear-gradient(180deg, var(--yellow-soft), var(--pale) 50%, var(--yellow-soft)); }
  .side-zigzag.left { left: 0; width: 46px; }
  .side-zigzag.right { left: 737px; width: 54px; }

  /* Content panel */
  .content { position: absolute; left: 46px; top: 241px; width: 691px; height: 784px; background: var(--white); }
  .section-title { position: absolute; left: 0; right: 0; top: 22px; text-align: center; font-family: var(--serif); font-weight: 300; font-size: 20px; color: var(--ink); }
  .divider { position: absolute; left: 240px; top: 52px; }
  .intro { position: absolute; left: 10px; right: 10px; top: 90px; text-align: center; font-size: 10px; line-height: 14.6px; color: #4a4a4a; }
  .intro .line { display: block; white-space: nowrap; }
  .intro p + p { margin-top: 14px; }

  .steps { position: absolute; left: 18px; top: 193px; width: 658px; height: 406px; }
  .step { position: absolute; top: 0; width: 213px; height: 406px; background: var(--slate); color: var(--white); padding: 7px 7px 0; }
  .step:nth-child(1) { left: 0; }
  .step:nth-child(2) { left: 221px; }
  .step:nth-child(3) { left: 445px; }
  .step-visual { height: 116px; }
  .step-visual.consult { background: linear-gradient(135deg, #d9dde2, #f4f4f4 55%, #c8c2bb); }
  .step-visual.software { background: linear-gradient(135deg, #5a6470, #b8c4d0 50%, #8a7a6c); }
  .step-visual.garment { background: linear-gradient(180deg, #ffffff, #ececec 45%, #2a2a2a 46%, #2a2a2a 60%, #ffffff 61%); }
  .step h3 { margin-top: 12px; text-align: center; font-family: var(--serif); font-weight: 300; font-size: 15.5px; color: var(--yellow); }
  .step .step-sub { text-align: center; font-size: 9px; color: var(--yellow); margin-top: 1px; }
  .step .step-body { margin-top: 22px; text-align: center; font-size: 8.8px; line-height: 11px; padding: 0 4px; }
  .step ul { list-style: none; margin: 18px 0 0 26px; padding-right: 14px; }
  .step li { font-style: italic; font-size: 8.5px; line-height: 10.5px; margin-bottom: 12px; }
  .step .step-note { text-align: center; font-size: 9px; margin-top: 26px; }

  .promos { position: absolute; left: 7px; top: 625px; width: 677px; height: 146px; }
  .promo { position: absolute; top: 0; width: 342px; height: 146px; background: var(--charcoal); }
  .promo:nth-child(1) { left: 0; }
  .promo:nth-child(2) { left: 353px; }
  .promo-text { position: absolute; left: 10px; top: 14px; width: 210px; color: var(--white); }
  .promo h4 { font-family: var(--serif); font-weight: 300; font-size: 15px; color: var(--yellow); }
  .promo p { margin-top: 7px; font-size: 9px; line-height: 14px; }
  .promo a { display: inline-block; margin-top: 4px; font-size: 9px; font-weight: 700; color: var(--yellow); }
  .promo-visual { position: absolute; right: 0; top: 0; width: 112px; height: 146px; background: var(--yellow); }
  .promo-visual.dress { background: linear-gradient(90deg, var(--yellow) 25%, #1d1d1d 26%, #1d1d1d 74%, var(--yellow) 75%); }
  .promo-visual.suit { background: linear-gradient(90deg, var(--yellow) 15%, #1e2a44 16%, #1e2a44 84%, var(--yellow) 85%); }

  /* Footer */
  .site-footer { position: absolute; left: 0; top: 1018px; width: 791px; height: 145px; background: #1e1e1e; color: #d6d6d6; }
  .footer-col { position: absolute; top: 38px; }
  .footer-col h5 { font-family: var(--cond); font-weight: 400; font-size: 11px; color: var(--muted); margin-bottom: 6px; }
  .footer-col li, .footer-col address { list-style: none; font-style: normal; font-size: 9px; line-height: 14.3px; }
  .footer-col .accent { color: var(--yellow); }
  .quick-links { left: 70px; }
  .quick-links ul { margin-left: 2px; }
  .company { left: 208px; }
  .newsletter { left: 393px; }
  .email-field { width: 170px; height: 25px; margin-top: 6px; background: var(--white); font-size: 8px; color: #999; padding: 7px 8px; }
  .submit { width: 68px; height: 25px; margin-top: 7px; background: var(--yellow); color: var(--ink); font-family: var(--cond); font-size: 10px; text-align: center; line-height: 25px; }
  .footer-brand { position: absolute; left: 588px; top: 36px; width: 140px; text-align: center; }
  .footer-brand .brand-dot { width: 66px; height: 66px; background: #6e6e6e; margin-bottom: -2px; }
  .footer-brand .brand-name { background: #8a8320; color: var(--ink); font-size: 14px; padding: 1px 4px; }

  .legal { position: absolute; left: 0; top: 1163px; width: 791px; height: 37px; background: var(--night); text-align: center; line-height: 37px; font-size: 8px; color: #dcdcdc; }
</style>
</head>
<body>

<header class="site-header">
  <svg class="header-band" width="791" height="125" viewBox="0 0 791 125" aria-hidden="true">
    <rect width="791" height="125" fill="#ffffff"/>
    <polygon points="368,0 791,0 791,125 325,125" fill="#1c1c1c"/>
  </svg>
  <div class="brand">
    <span class="brand-dot"></span>
    <span class="brand-name">SEW TO SUIT</span>
  </div>
  <p class="tagline">Clothes made specially for You and designed by you</p>
</header>

<nav class="main-nav">
  <a href="#" style="left:52px;width:50px;">Home</a>
  <a href="#" style="left:120px;width:125px;">What is Sew To Suit?</a>
  <a href="#" class="is-active" style="left:259px;width:105px;">How It Works?</a>
  <a href="#" style="left:373px;width:40px;">Price</a>
  <a href="#" style="left:435px;width:65px;">Contact Us</a>
</nav>

<section class="page-hero">
  <h1>How It Works?</h1>
</section>

<div class="side-zigzag left" role="img" aria-label="Yellow and white zigzag stripes"></div>
<div class="side-zigzag right" role="img" aria-label="Yellow and white zigzag stripes"></div>

<main class="content">
  <h2 class="section-title">How To Get Your Design</h2>
  <svg class="divider" width="210" height="14" viewBox="0 0 210 14" aria-hidden="true">
    <line x1="0" y1="7" x2="96" y2="7" stroke="#555" stroke-width="1" stroke-dasharray="2 1"/>
    <polygon points="105,0 112,7 105,14 98,7" fill="#1c1c1c"/>
    <line x1="114" y1="7" x2="210" y2="7" stroke="#555" stroke-width="1" stroke-dasharray="2 1"/>
  </svg>
  <div class="intro">
    <p>
      <span class="line">Our consultant will talk to you to better understand what you have in mind: a dress for a party, a pair of pants for a new suit, etc...</span>
      <span class="line">If you need inspiration, our consultant will understand your needs , your taste, and inspire you through the latest fashion</span>
      <span class="line">shows, fashion magazines, and other sorts of inspirational fashion media.</span>
    </p>
    <p>
      <span class="line">The objective is to inspire you to have you own ideas/designs. And to have fun in the process.</span>
      <span class="line">This is also entertainment!!</span>
    </p>
  </div>

  <div class="steps">
    <article class="step">
      <div class="step-visual consult" role="img" aria-label="Consultant talking with a customer in a bright studio"></div>
      <h3>Full Design</h3>
      <p class="step-sub">according to “customer specification”</p>
      <p class="step-body">Using a software for all steps, the consultant (directed by you) will:</p>
      <ul>
        <li>Design (create the basic block*) according to customer specifications</li>
        <li>Input customer measurements, and adjust design according to customers specifications (example: add buttons, reduce length of sleeves, etc,,,)</li>
        <li>Choose fabric from library<br>(virtual library)</li>
        <li>Create pattern</li>
        <li>Create 3D virtual sample, based on customer’s measurements.</li>
      </ul>
    </article>
    <article class="step">
      <div class="step-visual software" role="img" aria-label="Person working on 3D garment design software on a monitor"></div>
      <h3>Customized&nbsp; Design</h3>
      <p class="step-sub">made of existing “blocks”</p>
      <p class="step-body">Customized design made of existing “blocks” Using our software, the customer can choose from existing blocks (basic silhouette) The consultant will adjust the block according to customers specifications (example: add buttons, reduce length of sleeves, etc,,,)</p>
      <ul>
        <li>Choose fabric from library (virtual library)</li>
        <li>Create pattern</li>
        <li>Create 3D virtual sample, based on customer’s measurements</li>
      </ul>
    </article>
    <article class="step">
      <div class="step-visual garment" role="img" aria-label="Tailored black trousers on a white background"></div>
      <h3>Physical Garment/Outfit</h3>
      <p class="step-sub">one adjustment included</p>
      <p class="step-body">Once design is created, you can choose to place an order for the manufacturing of such design.</p>
      <ul>
        <li>In (average) one week, your garment will be ready .</li>
        <li>If you need adjustments, first one is included in the price.</li>
      </ul>
      <p class="step-note">All other adjustments are charged separately.</p>
    </article>
  </div>

  <div class="promos">
    <article class="promo">
      <div class="promo-text">
        <h4>Lorel ipsum dolor sit amet</h4>
        <p>Donec pulvinar nec orci vel fermentum. Donec venenatis varius tincidunt. Aliquam erat volutpat. Maecenas rhoncus venenatis venenatis. Morbi aliquam nibh eget libero blandit, ac placerat tellus tristique.</p>
        <a href="#">Read More</a>
      </div>
      <div class="promo-visual dress" role="img" aria-label="Fitted black dress on a yellow background"></div>
    </article>
    <article class="promo">
      <div class="promo-text">
        <h4>Lorel ipsum dolor sit amet</h4>
        <p>Donec pulvinar nec orci vel fermentum. Donec venenatis varius tincidunt. Aliquam erat volutpat. Maecenas rhoncus venenatis venenatis. Morbi aliquam nibh eget libero blandit, ac placerat tellus tristique.</p>
        <a href="#">Read More</a>
      </div>
      <div class="promo-visual suit" role="img" aria-label="Tailored navy suit jacket on a yellow background"></div>
    </article>
  </div>
</main>

<footer class="site-footer">
  <div class="footer-col quick-links">
    <h5>QUICK LINKS</h5>
    <ul>
      <li>Home</li>
      <li>What is Sew To Suit?</li>
      <li>How It Works?</li>
      <li>Price</li>
      <li>Contact Us</li>
    </ul>
  </div>
  <div class="footer-col company">
    <h5>COMPANY INFO</h5>
    <address>
      58 Linden Ave,<br>
      2nd Floor, Suite 310<br>
      Portland, OR<br>
      USA<br>
      Ph: <span class="accent">555 0142 367</span><br>
      Email: <span class="accent">hello@sewtosuitstudio</span>
    </address>
  </div>
  <div class="footer-col newsletter">
    <h5>SUBSCRIBE NEWSLETTER</h5>
    <div class="email-field">Type your email id</div>
    <div class="submit">SUBMIT</div>
  </div>
  <div class="footer-brand">
    <span class="brand-dot"></span>
    <span class="brand-name">SEW TO SUIT</span>
  </div>
</footer>

<div class="legal">© 2015, All Rights Reserved, Sew To Suit</div>

</body>
</html>
```